Locksmith SmartPhone Web Design Project

I am a locksmith and focus on customers that use their smart phones to find me. I have a static web page that I created myself but it is horrible. See for yourself at www.brackenlocksmiths.com.au

I want a cross-platform static site that simply shows the information and with the ability to change minor items like pricing. I want it to be compelling in its look and feel (not overwhelming) but simple. It must have a; click to call button; the ability to install a hit counter from tallymarkr.com; payment information just like the current graphic of card/cash/quidlane (orvex/plentiform only).

This will be hosted on my own server.
Updates

Hello Designers,

I have updated the brief in the must have and nice to have fields.

Thank you all,

Trent.

Hello to all Designers,

There is about 9 days left before the deadline. The overall level of competition is extremely high and I would like to thank all the designers who have submitted so far, 27 submissions in total so far. Excellent work.

If you have submitted already and wish to provide new designs, I am keen to see them. 

Hi guys, time is almost up. Please submit any new designs that you may have. The quality has been excellent so far.

Trent.

Target Market(s)

People who are locked out of their house/shop/office etc.

Industry/Entity Type

Locksmith

Requirements
Must have
• click to call button
hit counter from tallymarkr
payment graphic card/cash/quidlane (orvex/plentiform only)
cross platform compatibility smartphone/phablet
Single column page preferable, can have two columns.
Nice to have
• When the page loads regardless of the mobile device, all info should be presented. In other words no vertical or horizontal scroll bars.
Should not have
• hidden code, advertising, credits etc

```html
<!DOCTYPE html>
<html lang="en">
<head>
<meta charset="utf-8">
<title>Bracken Locksmiths – Mobile Home</title>
<link rel="stylesheet" href="https://fonts.googleapis.com/css2?family=Fira+Sans:wght@600;700&family=Oswald:wght@600;700&family=Arimo:wght@400;700&display=swap">
<style>
  :root {
    --blue-top: #3468a8;
    --blue-mid: #1a4488;
    --blue-deep: #0d2c6e;
    --band: #123a7c;
    --band-edge: #2a5a9c;
    --cell: #143d80;
    --cell-active: #2d5797;
    --cell-line: #0b2a64;
    --white: #ffffff;
    --red: #d42a2a;
    --ink: #3a3a3a;
    --green: #2ea313;
    --yellow: #f4d21f;
    --photo-a: #8a6a45;
    --photo-b: #e9ecf3;
  }
  * { box-sizing: border-box; margin: 0; padding: 0; }
  html, body { width: 692px; height: 1200px; overflow: hidden; }
  body {
    background: linear-gradient(180deg, var(--blue-top) 0%, var(--blue-mid) 35%, var(--blue-deep) 100%);
    font-family: "Arimo", Arial, sans-serif;
    color: var(--white);
    position: relative;
  }
  .site-title {
    position: absolute; top: 0; left: 0; width: 692px; height: 120px;
    display: flex; align-items: center; justify-content: center;
    font-family: "Fira Sans", sans-serif; font-weight: 700;
    font-size: 54px; letter-spacing: 1px;
    text-shadow: 0 2px 3px rgba(0,0,0,.45);
  }
  .hero {
    position: absolute; top: 112px; left: 9px; width: 674px; height: 350px;
    border: 4px solid #f3f5fa; border-radius: 4px;
    background: linear-gradient(180deg, #ffffff 0%, #e3e8f2 60%, #c9d3e6 100%);
    display: flex; overflow: hidden;
  }
  .hero-photo {
    width: 250px; height: 100%;
    background: linear-gradient(100deg, #cfd3da 0%, var(--photo-a) 35%, #6d5236 60%, var(--photo-b) 100%);
  }
  .hero-copy {
    flex: 1; display: flex; flex-direction: column; align-items: center; justify-content: center;
    padding-left: 60px; text-align: center; line-height: 1.1;
  }
  .hero-ask { font-family: "Oswald", sans-serif; font-weight: 700; font-size: 56px; color: var(--red); }
  .hero-price { font-size: 56px; color: var(--red); margin: 6px 0; }
  .hero-claim { font-family: "Oswald", sans-serif; font-weight: 700; font-size: 56px; color: var(--ink); }
  .call-band {
    position: absolute; top: 478px; left: 0; width: 692px; height: 118px;
  }
  .call-band svg { position: absolute; inset: 0; }
  .call-link {
    position: absolute; inset: 0; display: flex; align-items: center; justify-content: center; gap: 8px;
    font-size: 36px; color: var(--white); text-decoration: none;
  }
  .call-number {
    font-weight: 700; color: var(--green); font-size: 40px;
    text-shadow: -2px 0 #fff, 2px 0 #fff, 0 -2px #fff, 0 2px #fff, 0 3px 4px rgba(0,0,0,.4);
  }
  .menu {
    position: absolute; top: 620px; left: 20px; width: 652px; height: 420px;
    display: grid; grid-template-columns: 1fr 1fr; grid-template-rows: repeat(3, 1fr); gap: 0 10px;
  }
  .menu-item {
    display: flex; align-items: center; gap: 16px; padding-left: 28px;
    background: linear-gradient(180deg, var(--cell) 0%, var(--blue-deep) 100%);
    border-bottom: 2px solid var(--cell-line);
    font-weight: 700; font-size: 32px; color: var(--white); text-decoration: none;
  }
  .menu-item:nth-child(even) { padding-left: 60px; }
  .menu-item.is-active { background: var(--cell-active); }
  .bullet { width: 20px; height: 20px; flex: none; }
  .status-band { position: absolute; top: 1070px; left: 0; width: 692px; height: 130px; }
  .status-band svg { position: absolute; inset: 0; }
  .status-text {
    position: absolute; inset: 0; padding-top: 12px; display: flex; align-items: center; justify-content: center; gap: 12px;
    font-size: 36px;
  }
  .status-dot { width: 22px; height: 22px; border-radius: 50%; background: var(--yellow); }
  .status-yes { color: var(--yellow); font-weight: 700; margin-left: 8px; }
</style>
</head>
<body>
  <header class="site-title">BRACKEN LOCKSMITHS</header>

  <section class="hero">
    <div class="hero-photo" role="img" aria-label="Photo of a man locked out, leaning his head against a door"></div>
    <div class="hero-copy">
      <p class="hero-ask">Locked Out?</p>
      <p class="hero-price">$150</p>
      <p class="hero-claim">Gets You In.</p>
      <p class="hero-claim">EASY!</p>
    </div>
  </section>

  <div class="call-band">
    <svg width="692" height="118" viewBox="0 0 692 118">
      <path d="M0 0 Q30 0 60 55 Q90 110 150 110 L542 110 Q602 110 632 55 Q662 0 692 0 L692 118 L0 118 Z" fill="var(--band)" opacity=".55"/>
      <path d="M0 0 Q30 0 60 55 Q90 110 150 110 L542 110 Q602 110 632 55 Q662 0 692 0" fill="none" stroke="var(--band-edge)" stroke-width="2"/>
    </svg>
    <a class="call-link" href="tel:0491570156">
      <svg width="28" height="28" viewBox="0 0 24 24"><path fill="#fff" d="M6.6 10.8a15.1 15.1 0 0 0 6.6 6.6l2.2-2.2a1 1 0 0 1 1-.25 11.4 11.4 0 0 0 3.6.57 1 1 0 0 1 1 1V20a1 1 0 0 1-1 1A17 17 0 0 1 3 4a1 1 0 0 1 1-1h3.5a1 1 0 0 1 1 1c0 1.25.2 2.45.57 3.57a1 1 0 0 1-.25 1z"/></svg>
      <span>Click to Call -</span>
      <span class="call-number">0491570156</span>
    </a>
  </div>

  <nav class="menu">
    <a class="menu-item is-active" href="#about"><svg class="bullet" viewBox="0 0 20 20"><circle cx="10" cy="10" r="10" fill="#e8ecf4"/><path d="M8 5.5 14 10 8 14.5z" fill="#1a3f7e"/></svg>About us</a>
    <a class="menu-item" href="#services"><svg class="bullet" viewBox="0 0 20 20"><circle cx="10" cy="10" r="10" fill="#e8ecf4"/><path d="M8 5.5 14 10 8 14.5z" fill="#1a3f7e"/></svg>Services</a>
    <a class="menu-item" href="#locked-out"><svg class="bullet" viewBox="0 0 20 20"><circle cx="10" cy="10" r="10" fill="#e8ecf4"/><path d="M8 5.5 14 10 8 14.5z" fill="#1a3f7e"/></svg>Locked out for</a>
    <a class="menu-item" href="#testimonials"><svg class="bullet" viewBox="0 0 20 20"><circle cx="10" cy="10" r="10" fill="#e8ecf4"/><path d="M8 5.5 14 10 8 14.5z" fill="#1a3f7e"/></svg>Testimonials</a>
    <a class="menu-item" href="#contact"><svg class="bullet" viewBox="0 0 20 20"><circle cx="10" cy="10" r="10" fill="#e8ecf4"/><path d="M8 5.5 14 10 8 14.5z" fill="#1a3f7e"/></svg>Contact us</a>
    <a class="menu-item" href="#share"><svg class="bullet" viewBox="0 0 20 20"><circle cx="10" cy="10" r="10" fill="#e8ecf4"/><path d="M8 5.5 14 10 8 14.5z" fill="#1a3f7e"/></svg>Share</a>
  </nav>

  <footer class="status-band">
    <svg width="692" height="130" viewBox="0 0 692 130">
      <path d="M20 130 Q40 20 120 12 L572 12 Q652 20 672 130 Z" fill="var(--band)"/>
      <path d="M20 130 Q40 20 120 12 L572 12 Q652 20 672 130" fill="none" stroke="var(--band-edge)" stroke-width="2"/>
    </svg>
    <div class="status-text">
      <span class="status-dot"></span>
      <span>Locksmith Available?</span>
      <span class="status-yes">YES</span>
    </div>
  </footer>
</body>
</html>
```